Business Card for a mobile physiotherapy company

I need a layout for a business card for a mobile physiotherapy company.
Slogan is "Mobile Physiotherapy - Your Road To Recovery"
Phone number is 867-555-0142
Email VardenTherapy@postnest.ca (subject to change with website)
Website www.VardenTherapy.ca
My name and credentials: Luke Varden Luke Varden, BSc(kin), MPT, CAFCI, IMS
Information maybe included: Direct Billing, Services including Physiotherapy, IMS, acupuncture
Maybe include facebook and instagram logos
One side with the logo clean and sharp
Other side with details, try not to look too busy, keep everything concise

```html
<!DOCTYPE html>
<html lang="en">
<head>
<meta charset="utf-8">
<title>Varden Therapy – Business Card</title>
<link href="https://fonts.googleapis.com/css2?family=Crimson+Pro:wght@400;700&display=swap" rel="stylesheet">
<style>
  :root {
    --navy: #24426b;
    --green: #12503f;
    --paper: #f3f3f2;
    --backdrop: #bdbdbd;
    --ink: #2c3f5e;
    --white: #ffffff;
  }
  * { box-sizing: border-box; margin: 0; padding: 0; }
  html, body { width: 1200px; height: 576px; overflow: hidden; }
  body {
    background: var(--backdrop);
    font-family: "Crimson Pro", Georgia, serif;
    position: relative;
  }
  .card {
    position: absolute;
    height: 291px;
    background: var(--paper);
    border-radius: 12px;
    overflow: hidden;
    box-shadow: 0 2px 4px rgba(0,0,0,0.25);
  }
  .card--front { left: 82px; top: 139px; width: 485px; }
  .card--back { left: 602px; top: 138px; width: 480px; }

  .brand {
    position: absolute;
    display: flex;
    flex-direction: column;
    align-items: center;
  }
  .brand__mark {
    border-radius: 50%;
    background: var(--navy);
  }
  .brand__name {
    color: var(--navy);
    font-weight: 700;
    line-height: 1;
    white-space: nowrap;
  }

  .card--front .brand { left: 0; right: 0; top: 46px; }
  .card--front .brand__mark { width: 84px; height: 84px; }
  .card--front .brand__name { font-size: 38px; margin-top: 26px; }

  .services {
    position: absolute;
    left: 0; right: 0; top: 257px;
    text-align: center;
    font-size: 13.5px;
    color: var(--navy);
  }
  .services .sep { margin: 0 5px; }
  .front-band {
    position: absolute;
    left: 0; right: 0; bottom: 0;
    height: 7px;
    background: linear-gradient(90deg, var(--green), var(--navy));
  }

  .back-wave { position: absolute; left: 0; top: 0; width: 480px; height: 120px; }
  .tagline {
    position: absolute;
    right: 30px; top: 20px;
    text-align: right;
    color: var(--white);
    font-size: 14px;
    line-height: 17px;
  }
  .card--back .brand { left: 20px; width: 222px; top: 70px; }
  .card--back .brand__mark { width: 78px; height: 78px; }
  .card--back .brand__name { font-size: 33px; margin-top: 22px; }

  .person { position: absolute; right: 30px; top: 144px; text-align: right; color: var(--navy); }
  .person__name { font-size: 21px; font-weight: 700; letter-spacing: 0.5px; }
  .person__creds { font-size: 12px; margin-top: 1px; color: var(--ink); }

  .contact { position: absolute; right: 30px; top: 218px; list-style: none; }
  .contact li {
    display: flex; justify-content: flex-end; align-items: center;
    font-size: 13.5px; color: var(--ink); height: 17.5px;
  }
  .contact svg { width: 10px; height: 10px; margin-left: 8px; fill: var(--green); }

  .social { position: absolute; left: 48px; top: 248px; display: flex; align-items: center; font-size: 13.5px; color: var(--ink); }
  .social__dot { width: 19px; height: 19px; border-radius: 50%; margin-left: 6px; }
  .social__dot--a { background: var(--navy); }
  .social__dot--b { background: var(--green); }
</style>
</head>
<body>
  <section class="card card--front" aria-label="Card front">
    <div class="brand">
      <span class="brand__mark" aria-hidden="true"></span>
      <span class="brand__name">Varden Therapy</span>
    </div>
    <p class="services">Direct Billing<span class="sep">|</span>Services Including Physiotherapy<span class="sep">|</span>IMS<span class="sep">|</span>Acupuncture</p>
    <div class="front-band"></div>
  </section>

  <section class="card card--back" aria-label="Card back">
    <svg class="back-wave" viewBox="0 0 480 120" aria-hidden="true">
      <path d="M0 0 H480 V74 C420 82 360 62 300 38 C220 6 120 8 0 42 Z" fill="var(--navy)"/>
      <path d="M0 58 C110 18 210 22 290 52 C360 80 420 94 480 86 L480 100 C410 110 350 94 280 68 C200 38 100 36 0 72 Z" fill="var(--green)"/>
      <path d="M0 44 C60 22 140 14 240 30 C160 24 80 30 0 52 Z" fill="var(--green)"/>
    </svg>
    <p class="tagline">Mobile Physiotherapy<br>Your Road To Recovery</p>

    <div class="brand">
      <span class="brand__mark" aria-hidden="true"></span>
      <span class="brand__name">Varden Therapy</span>
    </div>

    <div class="person">
      <p class="person__name">LUKE VARDEN</p>
      <p class="person__creds">BSc(kin), MPT, CAFCI, IMS</p>
    </div>

    <ul class="contact">
      <li>867-555-0142
        <svg viewBox="0 0 10 10"><path d="M1 3 C1 1.5 3 1 5 1 C7 1 9 1.5 9 3 L7 3.6 L6.6 2.8 H3.4 L3 3.6 Z M2.5 4.5 H7.5 L8.5 9 H1.5 Z"/></svg>
      </li>
      <li>VardenTherapy@postnest.ca
        <svg viewBox="0 0 10 10"><path d="M0.5 2 H9.5 V8 H0.5 Z M1.2 2.6 L5 5.4 L8.8 2.6 V7.4 H1.2 Z" fill-rule="evenodd"/></svg>
      </li>
      <li>www.VardenTherapy.ca
        <svg viewBox="0 0 10 10"><circle cx="5" cy="5" r="4.3" fill="none" stroke="var(--green)" stroke-width="1"/><ellipse cx="5" cy="5" rx="1.8" ry="4.3" fill="none" stroke="var(--green)" stroke-width="0.8"/><path d="M0.7 5 H9.3" stroke="var(--green)" stroke-width="0.8"/></svg>
      </li>
    </ul>

    <div class="social">
      <span>Follow us on:</span>
      <span class="social__dot social__dot--a" aria-hidden="true"></span>
      <span class="social__dot social__dot--b" aria-hidden="true"></span>
    </div>
  </section>
</body>
</html>
```